Business Card Design

I already have a company logo for my company. I have a logo for the manufacturer we represent. I want a professional business card design.

```html
<!DOCTYPE html>
<html lang="en">
<head>
<meta charset="UTF-8">
<title>Beacon Guard LLC – Business Card</title>
<link href="https://fonts.googleapis.com/css2?family=Montserrat:wght@400;500;700;800&display=swap" rel="stylesheet">
<style>
  :root{
    --backdrop:#3b3b3d;
    --gold-top:#8c6c15;
    --gold-bottom:#6a5319;
    --accent-gold:#c99a1c;
    --card-black:#1d1d1f;
    --signal-red:#e3262d;
    --silver:#e4e4e4;
    --muted:#cfcfcf;
  }
  *{margin:0;padding:0;box-sizing:border-box}
  html,body{width:1200px;height:688px;overflow:hidden}
  body{
    background:var(--backdrop);
    font-family:'Montserrat',sans-serif;
    position:relative;
  }
  .card{
    position:absolute;
    top:196px;
    width:520px;
    height:297px;
    border-radius:3px;
    box-shadow:0 14px 30px rgba(0,0,0,.45);
    overflow:hidden;
  }
  .card--front{
    left:50px;
    background:linear-gradient(180deg,var(--gold-top) 0%,var(--gold-bottom) 100%);
    display:flex;align-items:center;justify-content:center;
  }
  .card--back{
    left:630px;
    background:var(--card-black);
  }
  .brand{
    display:flex;align-items:center;gap:12px;
    padding-bottom:8px;
    border-bottom:3px solid var(--accent-gold);
  }
  .brand__square{
    width:22px;height:22px;background:var(--signal-red);flex:none;
  }
  .brand__name{
    font-weight:800;
    font-size:30px;
    letter-spacing:1px;
    color:var(--silver);
    text-transform:uppercase;
    line-height:1;
  }
  .card--back .brand{
    position:absolute;left:38px;top:44px;
  }
  .card--back .brand__name{font-size:24px}
  .emblem-area{
    position:absolute;right:26px;top:26px;
    width:112px;height:112px;
    background:linear-gradient(160deg,#b08a22 0%,#5e4712 100%);
  }
  .stripes{
    position:absolute;right:0;top:150px;
    width:300px;height:90px;
  }
  .holder{
    position:absolute;left:40px;top:138px;
  }
  .holder__name{
    font-weight:700;font-size:19px;color:var(--signal-red);
  }
  .holder__role{
    font-size:11px;color:var(--muted);margin-top:2px;
  }
  .address{
    position:absolute;left:40px;top:196px;
    font-size:11px;line-height:15px;color:var(--muted);
  }
  .contact{
    position:absolute;left:40px;top:236px;
    list-style:none;font-size:11px;line-height:16px;color:var(--muted);
  }
  .contact li{display:flex;align-items:center;gap:8px}
  .contact svg{width:10px;height:10px;flex:none}
</style>
</head>
<body>

  <section class="card card--front" aria-label="Card front">
    <div class="brand">
      <span class="brand__square"></span>
      <span class="brand__name">Beacon Guard LLC</span>
    </div>
  </section>

  <section class="card card--back" aria-label="Card back">
    <div class="brand">
      <span class="brand__name">Beacon Guard LLC</span>
    </div>

    <div class="emblem-area" role="img" aria-label="Company emblem area"></div>

    <svg class="stripes" viewBox="0 0 300 90" aria-hidden="true">
      <polygon points="120,0 300,0 300,18 96,18" fill="var(--signal-red)"/>
      <polygon points="84,32 300,32 300,50 60,50" fill="var(--signal-red)"/>
      <polygon points="48,64 300,64 300,82 24,82" fill="var(--signal-red)"/>
    </svg>

    <div class="holder">
      <p class="holder__name">Dale Morgan</p>
      <p class="holder__role">Managing Director</p>
    </div>

    <p class="address">2410 Alder Ave<br>Boulder, CO 80302</p>

    <ul class="contact">
      <li>
        <svg viewBox="0 0 10 10" aria-hidden="true"><path d="M2 0.5 L3.8 2.6 L2.9 3.7 Q4 6 6.3 7.1 L7.4 6.2 L9.5 8 L8.3 9.5 Q3.5 8.8 0.5 1.7 Z" fill="var(--signal-red)"/></svg>
        555.214.0198
      </li>
      <li>
        <svg viewBox="0 0 10 10" aria-hidden="true"><rect x="0.5" y="2" width="9" height="6.5" fill="var(--signal-red)"/><path d="M0.5 2 L5 5.6 L9.5 2" stroke="var(--card-black)" stroke-width="0.9" fill="none"/></svg>
        info@beaconguardllc.com
      </li>
      <li>
        <svg viewBox="0 0 10 10" aria-hidden="true"><circle cx="5" cy="5" r="4.3" fill="none" stroke="var(--signal-red)" stroke-width="1.1"/><ellipse cx="5" cy="5" rx="1.8" ry="4.3" fill="none" stroke="var(--signal-red)" stroke-width="0.9"/><line x1="0.7" y1="5" x2="9.3" y2="5" stroke="var(--signal-red)" stroke-width="0.9"/></svg>
        www.beaconguardllc.com
      </li>
    </ul>
  </section>

</body>
</html>
```